The Brookhaven Sessions - Concert Series Website Design

I've recently decided to launch a concert series in my living room and would love a website to use to promote the series. I'm looking for a simple Wix design that I could take over once it's complete. I'll provide the logo for which I'd like the website to utilize the color scheme.

Target Market(s)

Music lovers in Denver

Industry/Entity Type

Music

Coding

Coded - Design and coding required

Number of Pages Required

2 page

Font styles to use
Script

Requirements
Must have
• 2 pages - one for concert goers to see the schedule and rsvp, and one for artists about the booking process

```html
<!DOCTYPE html>
<html lang="en">
<head>
<meta charset="UTF-8">
<title>The Brookhaven Sessions</title>
<link href="https://fonts.googleapis.com/css2?family=Great+Vibes&family=Josefin+Sans:wght@300;400&family=Poppins:ital,wght@0,400;0,500;0,600;1,400&display=swap" rel="stylesheet">
<style>
:root{
  --maroon:#7a2240;
  --plum:#2b0b3f;
  --deep:#1c0828;
  --orange:#f4a25a;
  --accent:#e08a3c;
  --grey:#f2f2f2;
  --ink:#222;
  --white:#fff;
  --black:#050505;
}
*{margin:0;padding:0;box-sizing:border-box}
html,body{width:1200px;height:4563px;overflow:hidden}
body{position:relative;font-family:"Poppins",sans-serif;color:var(--ink);background:var(--white)}
.abs{position:absolute}
.script{font-family:"Great Vibes",cursive;font-weight:400}
.caps{font-family:"Josefin Sans",sans-serif;font-weight:300;text-transform:uppercase}
.pair .script{margin-right:16px}
.btn{position:absolute;display:flex;align-items:center;justify-content:center;border-radius:22px;color:var(--white);font-size:13px;font-weight:600;text-transform:uppercase;background:linear-gradient(90deg,var(--maroon),var(--plum));letter-spacing:.2px;text-decoration:none}
.btn.orange{background:var(--orange);color:var(--deep)}
.rule{position:absolute;height:3px;width:100px;background:var(--accent)}
.body-copy{font-size:13px;line-height:24px;color:#333}

/* header */
.site-header{position:absolute;left:0;top:0;width:1200px;height:107px;background:var(--white)}
.brand{position:absolute;display:flex;align-items:center;gap:12px}
.brand .dot{width:56px;height:56px;border-radius:50%;background:var(--maroon);flex:none}
.brand .name{font-family:"Josefin Sans",sans-serif;font-weight:400;color:var(--maroon);font-size:21px;line-height:21px;text-transform:uppercase;white-space:nowrap}
.nav a{position:absolute;top:41px;font-size:14px;font-weight:500;color:#111;text-decoration:none}
.lang{position:absolute;left:746px;top:32px;display:flex;align-items:center;gap:10px;font-size:14px;font-weight:600}

/* hero */
.hero{position:absolute;left:0;top:107px;width:1200px;height:780px}
.hero-photo{position:absolute;inset:0;background:radial-gradient(ellipse at 78% 30%,#5a3d63 0%,#3a2048 35%,#1d0a2a 75%)}
.hero h1{position:absolute;left:0;width:1200px;text-align:center}
.hero .script{top:130px;font-size:84px;color:var(--orange);line-height:1}
.hero .caps{top:225px;font-size:62px;color:var(--white);letter-spacing:1px;line-height:1}
.hero p{position:absolute;left:310px;width:580px;top:314px;text-align:center;color:var(--white);font-size:16px;line-height:29px}

/* about */
.about-mark{position:absolute;left:142px;top:993px;width:425px;height:460px;display:flex;flex-direction:column;align-items:center;justify-content:center;gap:24px}
.about-mark .disc{width:230px;height:230px;border-radius:50%;background:var(--orange)}
.about-mark .name{font-family:"Josefin Sans",sans-serif;font-size:34px;line-height:36px;text-align:center;color:var(--maroon);text-transform:uppercase}
.heading-script{font-size:62px;line-height:1;color:var(--plum)}
.heading-caps{font-size:40px;line-height:1;color:#111}

/* shows */
.shows{position:absolute;left:0;top:1533px;width:1200px;height:887px;background:var(--grey)}
.show-card{position:absolute;left:186px;width:828px;height:142px;background:var(--white);border-radius:6px}
.show-card h3{position:absolute;left:34px;top:30px;font-size:17px;font-weight:600;color:#111}
.show-card .line{position:absolute;left:34px;top:60px;width:555px;height:1px;background:#bbb}
.show-card p{position:absolute;left:32px;top:74px;font-size:12.5px;color:#333}
.show-card .times{position:absolute;left:32px;top:99px;font-size:12px;color:var(--maroon)}
.show-card .btn{left:700px;top:35px;width:103px;height:42px}
.note{position:absolute;left:0;width:1200px;top:2279px;text-align:center;font-style:italic;font-size:13px}

/* expect */
.expect{position:absolute;left:0;top:2428px;width:1200px;height:700px;background:linear-gradient(100deg,#8b2a45 0%,#5c1b4e 45%,#2e0a43 100%)}
.expect .label{position:absolute;color:var(--white);font-size:16px;line-height:27px;font-weight:500}
.expect .label.r{text-align:right}

/* artist */
.artist-photo{position:absolute;left:633px;top:3191px;width:428px;height:428px;border-radius:50%;background:radial-gradient(circle at 40% 40%,#d49a5c 0%,#8c5a32 45%,#3a2316 100%)}

/* join */
.join{position:absolute;left:160px;top:3731px;width:880px;height:307px;background:linear-gradient(90deg,#f7a362,#e8774f)}
.join input{position:absolute;left:187px;top:182px;width:318px;height:43px;border-radius:22px;border:none;padding-left:34px;font-family:"Poppins",sans-serif;font-size:13px;color:#555;background:var(--white)}

/* footer */
.site-footer{position:absolute;left:0;top:3990px;width:1200px;height:573px}
.foot-col{position:absolute;top:294px;font-size:13px;color:var(--white);line-height:24px}
.foot-col h4{color:var(--accent);font-size:14px;font-weight:500;margin-bottom:14px}
.foot-rule{position:absolute;left:145px;top:485px;width:910px;height:1px;background:#444}
.copyright{position:absolute;left:0;width:1200px;top:514px;text-align:center;color:var(--white);font-size:13px}
</style>
</head>
<body>

<header class="site-header">
  <div class="brand" style="left:142px;top:20px">
    <span class="dot"></span>
    <span class="name">The<br>Brookhaven<br>Sessions</span>
  </div>
  <nav class="nav">
    <a style="left:430px">HOME</a>
    <a style="left:504px">CONCERTS</a>
    <a style="left:615px">FOR ARTISTS</a>
  </nav>
  <div class="lang">
    <svg width="34" height="34" viewBox="0 0 34 34" aria-hidden="true"><defs><clipPath id="flagClip"><circle cx="17" cy="17" r="17"/></clipPath></defs><g clip-path="url(#flagClip)"><rect width="34" height="34" fill="#fff"/><rect y="0" width="34" height="4" fill="#c8102e"/><rect y="8" width="34" height="4" fill="#c8102e"/><rect y="16" width="34" height="4" fill="#c8102e"/><rect y="24" width="34" height="4" fill="#c8102e"/><rect y="32" width="34" height="4" fill="#c8102e"/><rect width="16" height="18" fill="#1c3f8c"/></g></svg>
    <span>EN ▾</span>
  </div>
  <a class="btn" style="left:853px;top:28px;width:203px;height:43px">Reserve Your Seat</a>
</header>

<section class="hero">
  <div class="hero-photo" role="img" aria-label="Photo of a singer performing with an acoustic guitar in a dim room"></div>
  <h1 class="script">An Intimate</h1>
  <h1 class="caps">Night of Music</h1>
  <p>A curated living room concert series in Denver, bringing artists and audiences together in a space designed for connection, listening, and unforgettable performances.</p>
  <a class="btn" style="left:400px;top:459px;width:240px;height:42px">View Upcoming Shows</a>
  <a class="btn orange" style="left:651px;top:459px;width:149px;height:42px">RSVP Now</a>
  <svg class="abs" style="left:0;top:0" width="1200" height="780" viewBox="0 0 1200 780" aria-hidden="true">
    <defs><linearGradient id="bandGrad" x1="0" x2="1"><stop offset="0" stop-color="#7a2240"/><stop offset="1" stop-color="#2b0b3f"/></linearGradient></defs>
    <polygon points="0,616 600,721 1200,616 1200,780 0,780" fill="#fff"/>
    <polygon points="30,630 600,732 1170,630 600,776" fill="url(#bandGrad)"/>
  </svg>
</section>

<section class="about">
  <div class="about-mark" role="img" aria-label="The Brookhaven Sessions">
    <span class="disc"></span>
    <span class="name">The<br>Brookhaven Sessions</span>
  </div>
  <h2 class="script heading-script abs" style="left:641px;top:955px">Where Music</h2>
  <h2 class="caps heading-caps abs" style="left:641px;top:1036px">Feels Personal</h2>
  <span class="rule" style="left:641px;top:1091px"></span>
  <p class="body-copy abs" style="left:646px;top:1124px;width:420px">Lorem ipsum dolor sit amet, consectetur adipiscing elit, sed do eiusmod tempor incididunt ut labore et dolore magna aliqua. Ut enim ad minim veniam, quis nostrud exercitation ullamco laboris nisi ut aliquip ex ea commodo</p>
  <p class="body-copy abs" style="left:646px;top:1239px;width:420px">Lorem ipsum dolor sit amet, consectetur adipiscing elit, sed do eiusmod tempor incididunt ut labore et dolore magna aliqua. Ut enim ad minim veniam, quis nostrud exercitation ullamco laboris nisi ut aliquip ex ea commodo</p>
  <a class="btn" style="left:643px;top:1373px;width:202px;height:44px">Explore More</a>
</section>

<section class="shows">
  <h2 class="abs pair" style="left:0;width:1200px;top:100px;text-align:center;white-space:nowrap"><span class="script heading-script">Upcoming</span><span class="caps heading-caps">Shows</span></h2>
  <span class="rule" style="left:550px;top:193px"></span>
</section>
<article class="show-card" style="top:1774px"><h3>June 14 - The Modnight pines</h3><span class="line"></span><p>Lorem ipsum dolor sit amet, consectetur adipiscing elit, sed do eiusmod tempor incididunt ut</p><span class="times">Doors - 7.00 Am &nbsp;- &nbsp;Show 7.30 Pm</span><a class="btn">RSVP</a></article>
<article class="show-card" style="top:1931px"><h3>June 14 - The Modnight pines</h3><span class="line"></span><p>Lorem ipsum dolor sit amet, consectetur adipiscing elit, sed do eiusmod tempor incididunt ut</p><span class="times">Doors - 7.00 Am &nbsp;- &nbsp;Show 7.30 Pm</span><a class="btn">RSVP</a></article>
<article class="show-card" style="top:2088px"><h3>June 14 - The Modnight pines</h3><span class="line"></span><p>Lorem ipsum dolor sit amet, consectetur adipiscing elit, sed do eiusmod tempor incididunt ut</p><span class="times">Doors - 7.00 Am &nbsp;- &nbsp;Show 7.30 Pm</span><a class="btn">RSVP</a></article>
<p class="note">Private address shared after RSVP confirmation.</p>

<section class="expect" role="img" aria-label="Mountain range at dusk in maroon and purple tones">
  <h2 class="abs pair" style="left:0;width:1200px;top:102px;text-align:center;white-space:nowrap;color:#fff"><span class="script heading-script" style="color:#fff">What to</span><span class="caps heading-caps" style="color:#fff">Expect</span></h2>
  <span class="rule" style="left:550px;top:188px;background:#fff"></span>
  <svg class="abs" style="left:0;top:0" width="1200" height="700" viewBox="0 0 1200 700" aria-hidden="true">
    <path d="M 388,575 A 226 226 0 1 1 812,575" fill="none" stroke="#fff" stroke-width="7"/>
    <polygon points="0,700 600,536 1200,700" fill="#fff"/>
    <polyline points="160,665 600,528 1040,665" fill="none" stroke="#fff" stroke-width="2"/>
    <g fill="#6a2254" stroke="#fff" stroke-width="6">
      <circle cx="519" cy="284" r="36"/><circle cx="681" cy="284" r="36"/>
      <circle cx="406" cy="381" r="36"/><circle cx="794" cy="381" r="36"/>
      <circle cx="374" cy="500" r="36"/><circle cx="826" cy="500" r="36"/>
    </g>
    <g fill="none" stroke="#fff" stroke-width="2">
      <circle cx="519" cy="280" r="12"/><path d="M505,298 q14,-10 28,0"/>
      <rect x="667" y="272" width="28" height="18" rx="2"/><path d="M672,296 h18"/>
      <path d="M394,388 q12,-14 24,0 M400,374 l6,-8 l6,8 z"/>
      <circle cx="800" cy="374" r="7"/><path d="M795,379 l-12,14"/>
      <rect x="362" y="490" width="24" height="22" rx="2"/><path d="M362,497 h24 M368,486 v6 M380,486 v6"/>
      <circle cx="822" cy="496" r="9"/><path d="M829,503 l8,8"/>
    </g>
  </svg>
  <span class="label r" style="right:734px;top:231px">Community-driven<br>gatherings</span>
  <span class="label" style="left:739px;top:231px">Intimate, living-room<br>atmosphere</span>
  <span class="label r" style="right:861px;top:350px">BYOB-friendly<br>environment</span>
  <span class="label" style="left:858px;top:343px">Carefully curated<br>independent artists</span>
  <span class="label r" style="right:893px;top:487px">Limited seating</span>
  <span class="label" style="left:899px;top:478px">Attentive listening<br>audience</span>
</section>

<section class="artist">
  <h2 class="abs pair" style="left:145px;top:3198px;white-space:nowrap"><span class="script heading-script">Are You</span><span class="caps heading-caps">An Artist</span></h2>
  <span class="rule" style="left:145px;top:3281px"></span>
  <p class="body-copy abs" style="left:147px;top:3329px;width:415px">Lorem ipsum dolor sit amet, consectetur adipiscing elit, sed do eiusmod tempor incididunt ut labore et dolore magna aliqua. Ut enim ad minim veniam, quis nostrud exercitation ullamco laboris nisi ut aliquip ex ea commodo</p>
  <p class="body-copy abs" style="left:147px;top:3447px;width:415px">Lorem ipsum dolor sit amet, consectetur adipiscing elit, sed do eiusmod tempor incididunt ut labore et dolore magna aliqua. Ut enim ad minim veniam, quis nostrud exercitation ullamco laboris nisi ut aliquip ex ea commodo</p>
  <a class="btn" style="left:145px;top:3571px;width:201px;height:43px">Reserve Your Seat</a>
  <div class="artist-photo" role="img" aria-label="Photo of a smiling singer with headphones at a studio microphone"></div>
</section>

<section class="join">
  <h2 class="abs pair" style="left:0;width:880px;top:48px;text-align:center;white-space:nowrap"><span class="script heading-script">Join</span><span class="caps heading-caps">The List</span></h2>
  <p class="abs" style="left:0;width:880px;top:131px;text-align:center;font-size:15px;color:#222">Be the first to hear about new shows and special performances.</p>
  <input type="email" placeholder="Enter Email Address">
  <a class="btn" style="left:515px;top:182px;width:201px;height:43px">Join the List</a>
</section>

<footer class="site-footer">
  <svg class="abs" style="left:0;top:0" width="1200" height="573" viewBox="0 0 1200 573" aria-hidden="true">
    <defs><linearGradient id="footGrad" x1="0" x2="1"><stop offset="0" stop-color="#7a2240"/><stop offset="1" stop-color="#2b0b3f"/></linearGradient></defs>
    <polygon points="0,160 600,48 1200,160 1200,573 0,573" fill="#050505"/>
    <polygon points="40,160 600,55 1160,160 600,68" fill="url(#footGrad)"/>
  </svg>
  <div class="brand" style="left:489px;top:136px">
    <span class="dot" style="width:60px;height:60px"></span>
    <span class="name" style="color:#fff">The<br>Brookhaven<br>Sessions</span>
  </div>
  <div class="foot-col" style="left:145px"><h4>Quick Links</h4>Home<br>Upcoming Shows<br>RSVP<br>For Artists<br>Join the Guest List</div>
  <div class="foot-col" style="left:424px"><h4>Contact Us</h4>123, Lorum Opsum Dolor Sit,<br>Denver, Colorado<br><br>+1 (888) 888 - 8888<br><br>info@Companyname.com</div>
  <div class="foot-col" style="left:739px"><h4>Media</h4>Snapwall<br>Worklink<br>Friendspace</div>
  <div class="foot-col" style="left:931px"><h4>Other Links</h4>Privacy Policy<br>Terms &amp; Conditions</div>
  <span class="foot-rule"></span>
  <p class="copyright">Copyright@2026.All Rights Reserved.</p>
</footer>

</body>
</html>
```